Korvath Supply Website Redesign

Currently korvathsupply.example is focussed on fulfillment and transport from various products in the BBQ segment. However, no we want to update our business activities to Product Development, Brand Development, Online Positioning, Logistics & Aftersales, and Promotional BBQs. We will be a business for Outdoor Leisure Development from A to Z.

Therefore, we need a brand new website. The colours of the current website may be the same. However, i'd like to keep it clean. More white and use blue and green as accent colours. It is a business to business organization so the website should be looking formal and corporate. However we sell fun products so not too formal and corporate.

Pages we need; Home, About, Contact, Our Services (+ page per service) a place to share our news/blogs.

I have added some sort of mock up of an idea. However it needs some finetuning.

Target Market(s)

Businesses

Industry/Entity Type

Corporate/Logistics/Marketing

Coding

Coded - Design and coding required

Colors

Designer to choose colors to be used in the design.

Requirements
Must have
• Show clear distinguishing of the different services we provide (Product Development, Brand Development, Online Positioning, Logistics & Aftersales and Promotional BBQs). Every service should have its own page too. Besides, I would like to have a blog page to share relevant content.
Nice to have
• Show that we are the expert in Outdoor LEisure Development from A to Z
Should not have
• Be too informal. It may be semi-formal

```html
<!DOCTYPE html>
<html lang="en">
<head>
<meta charset="utf-8">
<title>Korvath Supply</title>
<link href="https://fonts.googleapis.com/css2?family=Raleway:wght@500;600;700&family=Roboto:wght@400;500;700&display=swap" rel="stylesheet">
<style>
:root{
  --navy:#0c2240;
  --green:#2f9a45;
  --teal:#2b6a64;
  --accent-blue:#2f6a85;
  --ink:#1d1d1f;
  --body:#3a3a3a;
  --field:#e4e5e7;
  --white:#ffffff;
}
*{margin:0;padding:0;box-sizing:border-box}
html,body{width:1200px;height:5277px;overflow:hidden;background:var(--white)}
body{font-family:'Roboto',sans-serif;color:var(--body);position:relative}
h1,h2,h3,h4{font-family:'Raleway',sans-serif}
.btn{position:absolute;display:inline-block;background:var(--teal);color:#fff;font:700 14px 'Raleway',sans-serif;padding:10px 20px;border-radius:3px;letter-spacing:.2px;text-transform:uppercase;white-space:nowrap}
.center-x{left:50%;transform:translateX(-50%)}

/* header */
.site-header{position:absolute;top:0;left:0;width:1200px;height:78px;background:#fff}
.brand{position:absolute;left:110px;top:19px;display:flex;align-items:center;gap:10px;font:700 32px 'Raleway',sans-serif;color:var(--accent-blue)}
.brand .dot{width:20px;height:20px;border-radius:50%;background:var(--green)}
.nav{position:absolute;top:25px;left:470px;font:500 14px 'Roboto',sans-serif;color:#222}
.nav a{position:absolute;white-space:nowrap}
.globe{position:absolute;left:950px;top:27px}
.login{position:absolute;left:1007px;top:17px;background:var(--teal);color:#fff;font:500 13px 'Roboto',sans-serif;padding:10px 16px;border-radius:3px;box-shadow:0 0 0 2px #cfe7d4}

/* hero */
.hero{position:absolute;top:78px;left:0;width:1200px;height:598px;border-bottom-left-radius:280px 230px;overflow:hidden;background:linear-gradient(180deg,#3a2a1c 0%,#5a4230 45%,#7d6650 75%,#4a3b2c 100%)}
.hero-shade{position:absolute;inset:0;background:rgba(20,12,6,.35)}
.hero h1{position:absolute;top:215px;width:100%;text-align:center;color:#fff;font-size:40px;font-weight:700;letter-spacing:.3px}
.hero p{position:absolute;top:278px;left:270px;width:660px;text-align:center;color:#fff;font-size:14px;line-height:26px}
.hero .btn{top:347px;background:var(--green);font-size:13px;padding:8px 14px}

/* about */
.about h2{position:absolute;top:755px;width:100%;text-align:center;font-size:29px;font-weight:700;color:var(--ink)}
.accent{color:var(--accent-blue)}
.about p{position:absolute;top:804px;left:185px;width:830px;text-align:center;font-size:14.5px;line-height:28.5px}
.about .btn{top:903px}

/* special */
.special{position:absolute;top:1024px;left:0;width:1200px;height:588px;background:var(--navy);border-top-right-radius:230px 200px;overflow:hidden}
.photo-circle{position:absolute;border-radius:50%}
.special .photo-circle{left:111px;top:76px;width:380px;height:380px;background:radial-gradient(circle at 55% 40%,#8c7668 0%,#5a4a42 45%,#2d3138 100%)}
.deco-ring{position:absolute;border-radius:50%;background:rgba(255,255,255,.05)}
.special h3{position:absolute;left:536px;top:106px;color:#fff;font-size:29px;font-weight:700}
.special .rule{position:absolute;left:751px;top:122px;width:88px;height:3px;background:var(--green)}
.special h2{position:absolute;left:510px;top:155px;color:var(--green);font-size:70px;font-weight:700;letter-spacing:.5px}
.special p{position:absolute;left:544px;top:254px;width:545px;color:#fff;font-size:14.5px;line-height:28.5px}
.special .btn{left:544px;top:422px}

/* services */
.services h2{position:absolute;top:1690px;width:100%;text-align:center;font-size:29px;font-weight:700;color:var(--ink)}
.services .lead{position:absolute;top:1740px;left:270px;width:660px;text-align:center;font-size:14.5px;line-height:28.5px}
.service-card{position:absolute;top:1843px;width:208px;height:332px;background:#fff;box-shadow:0 2px 12px rgba(0,0,0,.16);text-align:center}
.service-card .icon{width:96px;height:96px;border-radius:50%;background:#e3ecee;margin:28px auto 0;display:flex;align-items:center;justify-content:center}
.service-card .icon span{width:50px;height:50px;border-radius:50%;background:#b9cfd3}
.service-card h4{margin-top:20px;font-size:15.5px;font-weight:600;color:var(--accent-blue);white-space:nowrap}
.service-card p{margin:12px auto 0;width:176px;font-size:13.5px;line-height:24px}
.services .btn{top:2220px;box-shadow:0 0 0 2px #cfe7d4}

/* ensures */
.ensures{position:absolute;top:2341px;left:0;width:1200px;height:567px;background:var(--navy);border-top-left-radius:230px 200px;overflow:hidden}
.ensures h3{position:absolute;left:121px;top:126px;color:#fff;font-size:29px;font-weight:600}
.ensures .rule{position:absolute;left:565px;top:144px;width:92px;height:3px;background:var(--green)}
.ensures h2{position:absolute;left:121px;top:175px;color:var(--green);font-size:39px;font-weight:600}
.ensures p{position:absolute;left:121px;top:238px;width:545px;color:#fff;font-size:14.5px;line-height:28.5px}
.ensures .btn{left:121px;top:343px}
.ensures .photo-circle{left:749px;top:108px;width:336px;height:336px;background:radial-gradient(circle at 45% 45%,#c9d3dc 0%,#7d93a8 40%,#2e4a66 100%)}

/* blog */
.blog h2{position:absolute;top:2980px;width:100%;text-align:center;font-size:29px;font-weight:700;color:var(--ink)}
.blog .lead{position:absolute;top:3037px;left:270px;width:660px;text-align:center;font-size:14.5px;line-height:28.5px}
.post{position:absolute;background:#fff;box-shadow:0 2px 12px rgba(0,0,0,.15)}
.post .media{position:absolute;left:0;top:0}
.meta{display:flex;gap:28px;font-size:14px;color:#222;align-items:center}
.meta span{display:flex;align-items:center;gap:8px}
.post h4{font-size:19px;font-weight:600;color:var(--accent-blue);line-height:28px}
.post p{font-size:14px;line-height:27px;color:#333}
.post .more{display:inline-block;font:500 15px 'Roboto',sans-serif;color:var(--green);border-bottom:2px solid var(--green);padding-bottom:3px}
.post .body{position:absolute}

/* contact */
.contact{position:absolute;top:3983px;left:0;width:1200px;height:615px;background:var(--navy);border-top-right-radius:260px 200px;border-top-left-radius:40px 30px}
.contact h2{position:absolute;top:76px;width:100%;text-align:center;color:#fff;font-size:30px;font-weight:600}
.field{position:absolute;background:var(--field);border-radius:27px;font:500 12px 'Roboto',sans-serif;color:#111;padding:20px 22px;text-transform:uppercase}
.contact .btn{top:506px;left:537px;background:var(--green);padding:9px 18px}

/* partners */
.partners h2{position:absolute;top:4672px;width:100%;text-align:center;font-size:29px;font-weight:700;color:var(--ink)}
.partner{position:absolute;top:4764px;width:195px;height:76px;background:#fff;box-shadow:0 2px 10px rgba(0,0,0,.18);display:flex;align-items:center;justify-content:center;gap:8px;font:700 22px 'Raleway',sans-serif;color:var(--navy)}
.partner .mark{width:18px;height:18px;border-radius:50%;background:#c5303a}

/* footer */
.site-footer{position:absolute;top:4926px;left:0;width:1200px;height:351px;background:var(--navy);border-top-left-radius:150px 110px;color:#fff}
.site-footer .f-brand{position:absolute;left:112px;top:54px;display:flex;align-items:center;gap:10px;font:700 34px 'Raleway',sans-serif;color:#4c7488}
.site-footer .f-brand .dot{width:22px;height:22px;border-radius:50%;background:#3e6f5a}
.site-footer .about-text{position:absolute;left:112px;top:124px;width:260px;font-size:14px;line-height:28px}
.col{position:absolute;top:60px;font-size:14px;line-height:32px}
.col h4{font:600 18px 'Raleway',sans-serif;margin-bottom:4px}
.col .row{display:flex;gap:10px;align-items:flex-start;line-height:28px;margin-bottom:4px}
.socials{display:flex;gap:10px;margin-top:6px}
.socials span{width:24px;height:24px;border-radius:50%;background:var(--green)}
.site-footer .divider{position:absolute;left:112px;top:270px;width:1088px;height:1px;background:rgba(255,255,255,.2)}
.site-footer .copy{position:absolute;top:298px;width:100%;text-align:center;font-size:14px}
</style>
</head>
<body>

<header class="site-header">
  <div class="brand"><span class="dot"></span>Korvath Supply</div>
  <nav class="nav">
    <a style="left:0;font-weight:700">Home</a>
    <a style="left:92px">About Us</a>
    <a style="left:196px">Contact</a>
    <a style="left:293px">Our Services</a>
    <a style="left:422px">Blog</a>
  </nav>
  <svg class="globe" width="18" height="18" viewBox="0 0 18 18" fill="none" stroke="#2f9a45" stroke-width="1.4"><circle cx="9" cy="9" r="7.5"/><ellipse cx="9" cy="9" rx="3.2" ry="7.5"/><path d="M1.5 9h15M3 5h12M3 13h12"/></svg>
  <a class="login">LOG IN</a>
</header>

<section class="hero" role="img" aria-label="Photo of a warmly lit bar with shelves of bottles">
  <div class="hero-shade"></div>
  <h1>WELCOME TO KORVATH SUPPLY</h1>
  <p>Korvath Supply Group unburdens its customers through the silent distribution of their brand and associated products. We are strong in automation and have a lot of in-house</p>
  <a class="btn center-x">GET STARTED</a>
</section>

<section class="about">
  <h2>ABOUT TO <span class="accent">KORVATH SUPPLY</span></h2>
  <p>Korvath Supply Group unburdens its customers through a smooth distribution of their brand and associated products. Our strength lies in our automated processes and expertise in the field. This enables us to get products to the right place quickly and reliably. From small orders to larger complex customized deliveries.</p>
  <a class="btn center-x">READ MORE</a>
</section>

<section class="special">
  <div class="deco-ring" style="left:-60px;top:450px;width:200px;height:200px"></div>
  <div class="deco-ring" style="left:900px;top:-40px;width:130px;height:130px"></div>
  <div class="photo-circle" role="img" aria-label="Portrait photo of a smiling woman in glasses at a laptop"></div>
  <h3>WHAT MAKES</h3><div class="rule"></div>
  <h2>US SPECIAL</h2>
  <p>We believe that the partners we work for should be able to focus on building their brand and product. Korvath distribution unburdens the process from order processing to delivery. Together with our Partner Korvath Promotional, we can also support in the commercial process. . In more than 30 countries we have supplier relationships in both the retail and promotional products market.</p>
  <a class="btn">READ MORE</a>
</section>

<section class="services">
  <h2>OUR&nbsp; <span class="accent">SERVICES</span></h2>
  <p class="lead">Lorem ipsum dolor sit amet, consectetur adipiscing elit, sed do eiusmod tempor incididunt ut labore et dolore magna aliqua. Ut enim ad minim veniam, quis nostrud exercitation</p>
  <article class="service-card" style="left:52px">
    <div class="icon" role="img" aria-label="Product box icon"><span></span></div>
    <h4>Product Development</h4>
    <p>Lorem ipsum dolor sit amet, consectetur adipiscing elit, sed do eiusmod tempor incididunt ut labore.</p>
  </article>
  <article class="service-card" style="left:274px">
    <div class="icon" role="img" aria-label="Open book icon"><span></span></div>
    <h4>Online Positioning</h4>
    <p>Lorem ipsum dolor sit amet, consectetur adipiscing elit, sed do eiusmod tempor incididunt ut labore.</p>
  </article>
  <article class="service-card" style="left:496px">
    <div class="icon" role="img" aria-label="Light bulb idea icon"><span></span></div>
    <h4>Brand Development</h4>
    <p>Lorem ipsum dolor sit amet, consectetur adipiscing elit, sed do eiusmod tempor incididunt ut labore.</p>
  </article>
  <article class="service-card" style="left:718px">
    <div class="icon" role="img" aria-label="Delivery truck icon"><span></span></div>
    <h4>Logistics &amp; Aftersales</h4>
    <p>Lorem ipsum dolor sit amet, consectetur adipiscing elit, sed do eiusmod tempor incididunt ut labore.</p>
  </article>
  <article class="service-card" style="left:940px">
    <div class="icon" role="img" aria-label="Grill icon"><span></span></div>
    <h4>Promotional BBQs</h4>
    <p>Lorem ipsum dolor sit amet, consectetur adipiscing elit, sed do eiusmod tempor incididunt ut labore.</p>
  </article>
  <a class="btn center-x">MORE SERVICES</a>
</section>

<section class="ensures">
  <div class="deco-ring" style="left:60px;top:-30px;width:150px;height:150px"></div>
  <div class="deco-ring" style="left:1015px;top:470px;width:170px;height:170px"></div>
  <h3>KORVATH SUPPLY ENSURES</h3><div class="rule"></div>
  <h2>Silent Distributionus Special</h2>
  <p>ensures the smooth distribution of promotional merchandise products for its customers. With our own warehouse and fleet, we are able to get products to the right place quickly and reliably, from small orders to larger, complex</p>
  <a class="btn">READ MORE</a>
  <div class="photo-circle" role="img" aria-label="Photo of two colleagues looking at a screen in an office"></div>
</section>

<section class="blog">
  <h2>OUR <span class="accent">BLOG</span></h2>
  <p class="lead">Lorem ipsum dolor sit amet, consectetur adipiscing elit, sed do eiusmod tempor incididunt ut labore et dolore magna aliqua. Ut enim ad minim veniam, quis nostrud</p>

  <article class="post" style="left:180px;top:3146px;width:826px;height:280px">
    <div class="media" role="img" aria-label="Photo of colleagues discussing work at a desk" style="width:352px;height:280px;background:linear-gradient(135deg,#5d7893,#2d4560)"></div>
    <div class="body" style="left:408px;top:34px;width:390px">
      <div class="meta">
        <span><svg width="16" height="16" viewBox="0 0 16 16" fill="none" stroke="#555" stroke-width="1.4"><rect x="1.5" y="3" width="13" height="11.5" rx="1"/><path d="M1.5 7h13M5 1v4M11 1v4"/></svg>15.12.2021</span>
        <span><svg width="14" height="16" viewBox="0 0 14 16" fill="#555"><circle cx="7" cy="4.5" r="3.5"/><path d="M0 16c0-4 3-6.5 7-6.5s7 2.5 7 6.5z"/></svg>Post By Mara Voss</span>
      </div>
      <h4 style="margin-top:20px">Lorem ipsum dolor sit amet, consectetur adipiscing elit, sed do</h4>
      <p style="margin-top:8px">Sed ut perspiciatis unde omnis iste natus error sit voluptatem accusantium doloremque laudantium,rem</p>
      <a class="more" style="margin-top:10px">Read More</a>
    </div>
  </article>

  <article class="post" style="left:180px;top:3447px;width:404px;height:454px">
    <div class="media" role="img" aria-label="Photo of hands working with papers and a laptop on a desk" style="width:404px;height:192px;background:linear-gradient(135deg,#8a7062,#c9b9ae 55%,#6e7b8c)"></div>
    <div class="body" style="left:52px;top:230px;width:320px">
      <div class="meta">
        <span><svg width="16" height="16" viewBox="0 0 16 16" fill="none" stroke="#555" stroke-width="1.4"><rect x="1.5" y="3" width="13" height="11.5" rx="1"/><path d="M1.5 7h13M5 1v4M11 1v4"/></svg>15.12.2021</span>
        <span><svg width="14" height="16" viewBox="0 0 14 16" fill="#555"><circle cx="7" cy="4.5" r="3.5"/><path d="M0 16c0-4 3-6.5 7-6.5s7 2.5 7 6.5z"/></svg>Post By Mara Voss</span>
      </div>
      <h4 style="margin-top:14px">Lorem ipsum dolor sit amet, consectetur</h4>
      <p style="margin-top:6px">Sed ut perspiciatis unde omnis iste Lorem doloremque laudantium, totam rem aperiam,</p>
      <a class="more" style="margin-top:4px">Read More</a>
    </div>
  </article>

  <article class="post" style="left:602px;top:3447px;width:404px;height:454px">
    <div class="media" role="img" aria-label="Photo of a person with a laptop on a red mat on a wooden floor" style="width:404px;height:192px;background:linear-gradient(135deg,#6b3a26,#9a4a35 50%,#5a3020)"></div>
    <div class="body" style="left:52px;top:230px;width:320px">
      <div class="meta">
        <span><svg width="16" height="16" viewBox="0 0 16 16" fill="none" stroke="#555" stroke-width="1.4"><rect x="1.5" y="3" width="13" height="11.5" rx="1"/><path d="M1.5 7h13M5 1v4M11 1v4"/></svg>15.12.2021</span>
        <span><svg width="14" height="16" viewBox="0 0 14 16" fill="#555"><circle cx="7" cy="4.5" r="3.5"/><path d="M0 16c0-4 3-6.5 7-6.5s7 2.5 7 6.5z"/></svg>Post By Mara Voss</span>
      </div>
      <h4 style="margin-top:14px">Lorem ipsum dolor sit amet, consectetur</h4>
      <p style="margin-top:6px">Sed ut perspiciatis unde omnis iste Lorem doloremque laudantium, totam rem aperiam,</p>
      <a class="more" style="margin-top:4px">Read More</a>
    </div>
  </article>
</section>

<section class="contact">
  <h2>CONTACT US</h2>
  <div class="field" style="left:190px;top:156px;width:362px;height:53px">Name</div>
  <div class="field" style="left:575px;top:156px;width:359px;height:53px">Phone</div>
  <div class="field" style="left:190px;top:232px;width:362px;height:53px">Email</div>
  <div class="field" style="left:575px;top:232px;width:359px;height:53px">Subject</div>
  <div class="field" style="left:190px;top:310px;width:744px;height:151px">Message</div>
  <a class="btn">SUBMIT</a>
</section>

<section class="partners">
  <h2>OUR <span class="accent">PARTNERS</span></h2>
  <div class="partner" style="left:127px"><span class="mark" style="background:var(--navy)"></span>Korvath</div>
  <div class="partner" style="left:377px;color:#c5303a;font-weight:600">Sauce Hub</div>
  <div class="partner" style="left:627px"><span class="mark" style="background:#e0782a"></span>Ember Co</div>
  <div class="partner" style="left:879px;font-size:18px">Caskline</div>
</section>

<footer class="site-footer">
  <div class="f-brand"><span class="dot"></span>Korvath</div>
  <p class="about-text">Korvath Supply Group Distribution unburdens its customers through the silent distribution of their brand and associated products.</p>
  <div class="col" style="left:410px">
    <h4>LINK</h4>
    <div>Home</div><div>About Us</div><div>Contact</div><div>Our Services</div><div>Blog</div>
  </div>
  <div class="col" style="left:541px">
    <h4>CONTACT</h4>
    <div class="row"><svg width="12" height="16" viewBox="0 0 12 16" fill="#2f9a45" style="margin-top:6px"><path d="M6 0a6 6 0 0 0-6 6c0 4.5 6 10 6 10s6-5.5 6-10a6 6 0 0 0-6-6zm0 8.5A2.5 2.5 0 1 1 6 3.5a2.5 2.5 0 0 1 0 5z"/></svg><span>Harborline 40,<br>5521 TN Veldhaven</span></div>
    <div class="row"><svg width="14" height="14" viewBox="0 0 14 14" fill="#2f9a45" style="margin-top:7px"><path d="M3 0l2.5 3.5-1.5 2a8 8 0 0 0 4.5 4.5l2-1.5L14 11l-1.5 2.5C6 14 0 8 .5 1.5z"/></svg><span>+31 (0)20 555 0148</span></div>
    <div class="row"><svg width="15" height="12" viewBox="0 0 15 12" style="margin-top:8px"><path d="M0 0h15v12H0z" fill="#2f9a45"/><path d="M1.5 1.5l6 5 6-5" stroke="#0c2240" stroke-width="1.2" fill="none"/></svg><span>info@korvathsupply.example</span></div>
  </div>
  <div class="col" style="left:788px">
    <h4>HELP LINK</h4>
    <div>Terms&amp;condtions</div><div>Privacy Policy</div><div>Support</div>
  </div>
  <div class="col" style="left:956px">
    <h4>FOLLOW US</h4>
    <div class="socials"><span></span><span></span><span></span><span></span></div>
  </div>
  <div class="divider"></div>
  <p class="copy">©Copyrights 2021 korvathsupply | All Rights Reserved</p>
</footer>

</body>
</html>
```